Design a New Business Card for Our Company

We are looking for fresh, unique, and a modern business card that reflects our roots as digital marketing agency focused on SEM.

Industry/Entity Type

Marketing

Contact Information for Business Card

looking for very unique out of the box designs. clean and modern that compliments our logo

Requirements
Must have
• colors should match our logo
• Front should have name, address, email, and phone/fax of the person, phone/fax are the same number
• back should have our url

```html
<!DOCTYPE html>
<html lang="en">
<head>
<meta charset="utf-8">
<title>Lumora – Business Card</title>
<link rel="stylesheet" href="https://fonts.googleapis.com/css2?family=Poppins:wght@600&family=Open+Sans:wght@400;600&display=swap">
<style>
  :root {
    --brand-blue: #5f98d2;
    --brand-grey: #a9a9aa;
    --ink: #222222;
    --card-white: #ffffff;
    --backdrop: #ecebe8;
  }
  * { margin: 0; padding: 0; box-sizing: border-box; }
  html, body { width: 1200px; height: 900px; overflow: hidden; }
  body {
    background: var(--backdrop);
    position: relative;
    font-family: "Open Sans", Arial, sans-serif;
  }
  .card {
    position: absolute;
    border-radius: 16px;
    overflow: hidden;
    box-shadow: 0 6px 18px rgba(0,0,0,0.12);
  }

  /* Front */
  .card--front {
    left: 78px; top: 35px; width: 588px; height: 362px;
    background: var(--card-white);
  }
  .front-band {
    position: absolute; left: 0; top: 28px; width: 100%; height: 99px;
    background: var(--brand-blue);
  }
  .front-badge {
    position: absolute; left: 227px; top: -5px; width: 136px; height: 136px;
    border-radius: 50%; background: var(--card-white);
  }
  .wordmark {
    position: absolute; left: 0; width: 100%; text-align: center;
    font-family: "Poppins", Arial, sans-serif; font-weight: 600;
    letter-spacing: -1px;
  }
  .card--front .wordmark {
    top: 140px; font-size: 58px; line-height: 70px; color: var(--brand-grey);
    left: -10px;
  }
  .holder { position: absolute; left: 37px; top: 229px; }
  .holder-name { font-size: 21px; font-weight: 600; color: var(--brand-blue); line-height: 28px; }
  .holder-title { font-size: 15px; color: var(--ink); line-height: 18px; }
  .holder-address { margin-top: 14px; font-size: 15px; color: var(--ink); line-height: 19px; font-style: normal; }
  .contact-list {
    position: absolute; right: 36px; top: 261px; list-style: none;
    font-size: 15px; color: var(--ink); text-align: right;
  }
  .contact-list li { display: flex; justify-content: flex-end; align-items: center; height: 24px; gap: 9px; }
  .contact-list svg { width: 12px; height: 12px; fill: var(--brand-blue); }

  /* Back */
  .card--back {
    left: 390px; top: 507px; width: 564px; height: 348px;
    background: var(--brand-blue);
  }
  .back-stripe {
    position: absolute; left: 0; top: 80px; width: 100%; height: 96px;
    background: var(--card-white);
  }
  .back-badge {
    position: absolute; left: 219px; top: 61px; width: 132px; height: 132px;
    border-radius: 50%; background: var(--brand-blue);
  }
  .card--back .wordmark {
    top: 196px; font-size: 58px; line-height: 70px; color: var(--card-white);
  }
  .back-url {
    position: absolute; left: 0; width: 100%; top: 292px; text-align: center;
    font-size: 15px; color: var(--card-white);
  }
</style>
</head>
<body>

<section class="card card--front" aria-label="Business card front">
  <div class="front-band">
    <div class="front-badge"></div>
  </div>
  <div class="wordmark">lumora</div>

  <div class="holder">
    <p class="holder-name">Daniel Harper</p>
    <p class="holder-title">Managing Director</p>
    <address class="holder-address">48 Harbour Lane, Suite 6<br>Westbury, 204816</address>
  </div>

  <ul class="contact-list">
    <li>(021)-387-5164
      <svg viewBox="0 0 24 24" aria-hidden="true"><path d="M6.6 10.8a15.1 15.1 0 0 0 6.6 6.6l2.2-2.2a1 1 0 0 1 1-.25 11.4 11.4 0 0 0 3.6.57 1 1 0 0 1 1 1V20a1 1 0 0 1-1 1A17 17 0 0 1 3 4a1 1 0 0 1 1-1h3.5a1 1 0 0 1 1 1c0 1.25.2 2.45.57 3.57a1 1 0 0 1-.25 1z"/></svg>
    </li>
    <li>214-387-5160
      <svg viewBox="0 0 24 24" aria-hidden="true"><path d="M7 2h9v5H7zM4 8h16a2 2 0 0 1 2 2v10a2 2 0 0 1-2 2H4a2 2 0 0 1-2-2V10a2 2 0 0 1 2-2zm2 3v2h2v-2zm4 0v2h2v-2zm4 0v2h4v-2zM6 15v2h2v-2zm4 0v2h2v-2zm4 0v5h4v-5z"/></svg>
    </li>
    <li>daniel@lumora.com
      <svg viewBox="0 0 24 24" aria-hidden="true"><path d="M2 5h20v14H2zm2 2v.5l8 5 8-5V7zm0 2.8V17h16V9.8l-8 5z"/></svg>
    </li>
  </ul>
</section>

<section class="card card--back" aria-label="Business card back">
  <div class="back-stripe"></div>
  <div class="back-badge"></div>
  <div class="wordmark">lumora</div>
  <p class="back-url">www.lumora.com</p>
</section>

</body>
</html>
```